Email Marketing Campaign Brief

We want to do an email marketing campaign around our consulting services. The attached documents provide back ground on our work but additional copy can be found below:

KV7lr is committed to helping you, the educator, make informed buying decisions based on local control and independent reviews through a simple, impartial and an effective approach.
In education, there exists a vast array of educational solutions – such as reading, science, language arts, and math curricula; school-wide reform programs; interventions; after-school programs; and new educational technologies. In the marketplace, providers could, and most do, claim to be able to improve educational outcomes and, in many cases, they all pretend to be supported by evidence. But a cursory review reveals that most evidence consists of poorly designed or advocacy-driven studies with some providers having such inadequate research as could only be described as case studies.

So the problem for State and local education officials is that they must sort through a myriad of such claims to decide which solutions merit consideration for their schools and classrooms. One US official stated the problem saying “many of these practitioners have seen interventions (solutions), introduced with great fanfare as being able to produce dramatic gains, come and go over the years, yielding little in the way of positive and lasting change – a perception confirmed by the flat achievement results over the past 30 years in the Federal Survey of Scholastic Attainment long-term trend”

KV7lr is a process by which we make you, the educator, the locus of control

OUR Approach:
With four simple, yet highly effective steps, KV7lr guides educators through an informed buying process that’s based on local control and review.

Step 1 — Research, Review, and Evaluation Criteria

Step 2 — Cost / Benefit Analysis

Step 3 — Education Survey & Culture Scan

Step 4 — Negotiation & Representation

Target Market(s)

Education

Industry/Entity Type

Marketing

Font styles to use
Sans Serif

Colors
f9b46a
f37122

Requirements
Must have
• HTML format that can be used in an Email Campaign
Nice to have
• Additional Copy in Word

```html
<!DOCTYPE html>
<html lang="en">
<head>
<meta charset="utf-8">
<title>KV7lr – Informed Buying for Educators</title>
<link rel="stylesheet" href="https://fonts.googleapis.com/css2?family=Baloo+2:wght@600;800&family=Quicksand:wght@400;500&family=Open+Sans:wght@400;700&display=swap">
<style>
:root{
  --orange:#f37122;
  --orange-light:#f9b46a;
  --amber:#f7a21b;
  --red:#d4373a;
  --cyan:#1cb8e4;
  --green:#237f63;
  --blue:#1a9ad8;
  --burnt:#e8501c;
  --ink:#2b2b2b;
  --grey:#555;
  --white:#fff;
}
*{margin:0;padding:0;box-sizing:border-box}
html,body{width:702px;height:1200px;overflow:hidden;background:var(--white)}
.canvas{position:relative;width:702px;height:1200px;font-family:"Open Sans",Arial,sans-serif;color:var(--ink)}
.abs{position:absolute}

/* top navigation tabs */
.tabs{left:0;top:0;width:702px;height:52px}
.tab-label{position:absolute;top:10px;font-family:"Baloo 2",sans-serif;font-weight:800;font-size:19px;color:var(--white)}

/* brand block */
.brand{left:0;top:24px;width:244px;height:80px}
.brand-box{left:0;top:24px;width:244px;height:80px}
.brand-mark{position:absolute;left:40px;top:32px;width:16px;height:16px;background:var(--white);border-radius:50%}
.brand-name{position:absolute;left:62px;top:24px;font-family:"Quicksand",sans-serif;font-weight:500;font-size:30px;color:var(--white);line-height:1}

/* hero */
.hero{left:24px;top:76px;width:654px;height:306px;border-radius:0 0 50% 50% / 0 0 9% 9%;
  background:radial-gradient(ellipse at 30% 30%,#f3d1b4 0%,#e6b48f 30%,transparent 60%),
             radial-gradient(ellipse at 75% 40%,#f5dcc4 0%,#d9a57f 35%,transparent 65%),
             linear-gradient(160deg,#6fb1d8 0%,#c9dbe6 40%,#b9c77a 75%,#d9a64a 100%)}
.hero-title{left:0;width:702px;top:310px;text-align:center;font-family:"Baloo 2",sans-serif;font-weight:800;font-size:27px;color:var(--white);text-shadow:0 1px 3px rgba(0,0,0,.55)}
.hero-sub{left:0;width:702px;top:344px;text-align:center;font-family:"Baloo 2",sans-serif;font-weight:800;font-size:17px;color:var(--white);text-shadow:0 1px 3px rgba(0,0,0,.55)}

/* intro copy */
.intro{top:399px;width:284px;font-size:6.8px;line-height:9.2px;text-align:justify;color:#222}
.intro .gap{margin-top:6px}
.hl{color:var(--orange);font-weight:700}

/* approach */
.approach-title{left:0;width:702px;top:504px;text-align:center;font-family:"Baloo 2",sans-serif;font-weight:800;font-size:17px;color:#333}
.approach-sub{left:0;width:702px;top:523px;text-align:center;font-size:10px;line-height:12.5px;color:#444}

.shapes{left:0;top:0;width:702px;height:1200px}
.step-title{font-family:"Quicksand",sans-serif;font-weight:400;font-size:17px;line-height:21px;color:var(--white);text-align:center;text-transform:uppercase;white-space:nowrap}
.step-title.compact{font-size:15.5px}
.points{list-style:none;font-family:"Quicksand",sans-serif;font-weight:500;font-size:8.6px;line-height:11px;color:var(--white)}
.points li{position:relative;padding-left:11px;margin-bottom:11px}
.points li::before{content:"";position:absolute;left:1px;top:2px;width:6px;height:6px;border-radius:50%;background:var(--white);opacity:.85}
.points.centered{text-align:center}
.points.centered li{padding-left:0;margin-bottom:0}
.points.centered li::before{content:none}
.dot{display:inline-block;width:6px;height:6px;border-radius:50%;background:var(--white);opacity:.85;margin-right:4px;vertical-align:0}
.read-more{display:block;background:var(--white);color:var(--orange);font-family:"Quicksand",sans-serif;font-weight:500;font-size:10px;line-height:20px;text-align:center}

/* closing */
.impl-title{left:0;width:702px;top:1009px;text-align:center;font-family:"Baloo 2",sans-serif;font-weight:800;font-size:22px;color:var(--orange);letter-spacing:.3px}
.impl-sub{left:0;width:702px;top:1035px;text-align:center;font-size:12.5px;color:#333}
.cta{left:0;width:702px;top:1069px;text-align:center;font-size:12px;line-height:16px;color:#333}
.cta strong{font-weight:700}
.footer{left:50px;top:1112px;width:606px;height:48px;background:var(--orange);border-top:3px solid var(--orange-light)}
.footer-text{position:absolute;left:12px;top:14px;font-size:10px;color:var(--white)}
.footer-text b{font-family:"Baloo 2",sans-serif;font-weight:800;font-size:15px;margin-left:6px;vertical-align:-1px}
.social{position:absolute;top:10px;width:26px;height:26px;background:var(--white);border-radius:3px}
.web{right:100px;top:1166px;font-size:10px;font-weight:700;color:#333}
</style>
</head>
<body>
<div class="canvas">

  <svg class="abs tabs" viewBox="0 0 702 52" aria-hidden="true">
    <polygon points="216,0 405,0 382,52 216,52" fill="var(--amber)"/>
    <polygon points="405,0 565,0 542,52 382,52" fill="var(--red)"/>
    <polygon points="565,0 702,0 702,52 542,52" fill="var(--cyan)"/>
  </svg>
  <span class="tab-label" style="left:260px">Research</span>
  <span class="tab-label" style="left:444px">Policy</span>
  <span class="tab-label" style="left:592px">Practice</span>

  <svg class="abs brand" viewBox="0 0 244 80" aria-hidden="true">
    <polygon points="0,0 218,0 244,40 218,80 0,80" fill="var(--burnt)"/>
  </svg>
  <div class="abs brand-box">
    <span class="brand-mark"></span>
    <span class="brand-name">KV7lr</span>
  </div>

  <div class="abs hero" role="img" aria-label="Photo of smiling young children huddled together looking down into the camera"></div>
  <div class="abs hero-title">We help you to build geniuses</div>
  <div class="abs hero-sub">Research, Teaching, Learning</div>

  <div class="abs intro" style="left:56px">
    <p><span class="hl">KV7lr</span> is committed to helping you, the educator; make informed buying decisions based on local control and independent reviews through a simple, impartial and an effective approach.</p>
    <p>In education, there exists a vast array of educational solutions – such as reading, science, language arts, and math curricula; school-wide reform programs; interventions; after-school programs; and new educational technologies. In the marketplace, providers could, and most do, claim to be able to improve educational outcomes and, in many cases, they all pretend to be supported by evidence. But a cursory review reveals that most evidence consists of poorly designed or advocacy-driven studies with some providers having such inadequate research as could only be described as case studies.</p>
  </div>
  <div class="abs intro" style="left:360px">
    <p>So the problem for State and local education officials is that they must sort through a myriad of such claims to decide which solutions merit consideration for their schools and classrooms.</p>
    <p>One US official stated the problem saying “many of these practitioners have seen interventions (solutions), introduced with great fanfare as being able to produce dramatic gains, come and go over the years, yielding little in the way of positive and lasting change – a perception confirmed by the flat achievement results over the past 30 years in the Federal Survey of Scholastic Attainment long-term trend”.</p>
    <p class="gap"><span class="hl">KV7lr</span> is a process by which we make you, the educator, the focus of control.</p>
  </div>

  <div class="abs approach-title">OUR Approach:</div>
  <div class="abs approach-sub">With four simple, yet highly effective steps, KV7lr guides educators through<br>an informed buying process that’s based on local control and review.</div>

  <svg class="abs shapes" viewBox="0 0 702 1200" aria-hidden="true">
    <path d="M18,582 C60,560 100,598 142,580 C180,564 205,588 234,572 L234,834 Q150,842 26,852 Q18,760 18,582Z" fill="var(--green)"/>
    <path d="M244,598 l6,-3 6,3 6,-2 6,3 6,-3 6,2 6,-3 6,3 6,-2 6,3 6,-3 6,2 6,-3 6,3 6,-2 6,3 6,-3 6,2 6,-3 6,3 6,-2 6,3 6,-3 6,2 6,-3 6,3 6,-2 6,3 6,-3 6,2 6,-3 6,3 6,-2 6,3 2,-1 L458,824 L244,824Z" fill="var(--burnt)"/>
    <path d="M470,578 C510,598 540,566 580,574 C620,584 652,560 690,572 Q688,760 682,852 Q570,842 476,836Z" fill="var(--blue)"/>
    <path d="M190,830 Q350,818 508,830 Q514,900 506,958 Q350,968 192,962 Q182,900 190,830Z" fill="var(--amber)"/>
    <g font-family="Baloo 2, sans-serif" font-weight="800" font-size="30" fill="var(--red)" text-anchor="middle">
      <circle cx="52" cy="572" r="23" fill="#fff" stroke="var(--orange)" stroke-width="3"/><text x="52" y="584">1</text>
      <circle cx="350" cy="600" r="22" fill="#fff" stroke="var(--orange)" stroke-width="3"/><text x="350" y="612">2</text>
      <circle cx="640" cy="572" r="23" fill="#fff" stroke="var(--orange)" stroke-width="3"/><text x="640" y="584">3</text>
      <circle cx="350" cy="822" r="21" fill="#fff" stroke="var(--orange)" stroke-width="3"/><text x="350" y="834">4</text>
    </g>
    <g fill="none" stroke="#fff" stroke-width="2">
      <circle cx="44" cy="804" r="7"/><line x1="49" y1="809" x2="57" y2="818"/>
      <path d="M292,771 a6,6 0 1 1 10,0 l-1,5 h-8z"/><line x1="294" y1="780" x2="301" y2="780"/>
      <line x1="297" y1="758" x2="297" y2="761"/><line x1="285" y1="770" x2="288" y2="770"/><line x1="306" y1="770" x2="309" y2="770"/>
      <circle cx="552" cy="811" r="8" stroke-width="3" stroke-dasharray="3 2"/><circle cx="552" cy="811" r="5"/>
      <rect x="276" y="936" width="28" height="17" rx="1"/><line x1="270" y1="957" x2="310" y2="957"/>
    </g>
    <line x1="164" y1="974" x2="528" y2="974" stroke="#444" stroke-width="1"/>
    <polygon points="272,975 432,975 352,1006" fill="var(--orange-light)"/>
    <line x1="164" y1="1060" x2="528" y2="1060" stroke="#444" stroke-width="1"/>
  </svg>

  <section class="abs" style="left:18px;top:610px;width:216px">
    <h2 class="step-title">Research, Review, and<br>Evaluation Criteria</h2>
    <ul class="points" style="margin:10px 0 0 14px">
      <li>District needs analysis</li>
      <li>Program reviews and alignment to need</li>
      <li>Independent evaluation / data informed decisions</li>
    </ul>
  </section>
  <a class="abs read-more" style="left:68px;top:800px;width:66px">READ MORE</a>

  <section class="abs" style="left:244px;top:632px;width:214px">
    <h2 class="step-title compact">Cost / Benefit Analysis</h2>
    <ul class="points" style="margin:9px 24px 0 14px">
      <li>Cost alignmen At based on research, review and evaluation of programs</li>
      <li>Program cost by product offering and alignment to identified needs</li>
      <li>Sumary of cost, data and return on investment</li>
    </ul>
  </section>
  <a class="abs read-more" style="left:318px;top:767px;width:66px">READ MORE</a>

  <section class="abs" style="left:470px;top:610px;width:220px">
    <h2 class="step-title">Education Survey<br>and Culture Scan</h2>
    <ul class="points" style="margin:10px 0 0 8px;letter-spacing:-.1px">
      <li>District observation and perception survey</li>
      <li>Culture scan to identify education best practices</li>
      <li>Match to strategic plan goals and objectives</li>
    </ul>
  </section>
  <a class="abs read-more" style="left:574px;top:800px;width:66px">READ MORE</a>

  <section class="abs" style="left:184px;top:846px;width:328px">
    <h2 class="step-title">Negotiation<br>and Representation</h2>
    <ul class="points centered" style="margin-top:7px">
      <li><span class="dot"></span>Conduct Provider review and presentation</li>
      <li><span class="dot"></span>Representation for content and program negotiations</li>
      <li><span class="dot"></span>Support district in independent decision-marketing process</li>
    </ul>
  </section>
  <a class="abs read-more" style="left:318px;top:935px;width:64px">READ MORE</a>

  <div class="abs impl-title">PROGRAM IMPLEMENTATION</div>
  <div class="abs impl-sub">Independent Review Connected to School District Need and Stakeholder</div>
  <div class="abs cta">Let <span class="hl">KV7lr</span> help you make informed buying decisions.<br><strong>Contact us today for a no-cost consultation</strong></div>

  <footer class="abs footer">
    <div class="footer-text">Have a question? Is to great to listen you: <b>555.218.0467</b></div>
    <span class="social" style="left:450px"></span>
    <span class="social" style="left:482px"></span>
    <span class="social" style="left:514px"></span>
    <span class="social" style="left:546px"></span>
  </footer>
  <div class="abs web">www.KV7lr.com</div>

</div>
</body>
</html>
```